Custom Manufacturing Company square space website design

I own a custom manufacturing company that uses precision cutting technology to manufacture project components over a couple industries. We have an industrial CNC router and state of the art edge bander and cut a lot of cabinetry components for cabinet shops, builders, closet companies, ect. We offer design and assembly for any cabinetry or can build cabinets to spec. We also cut components for other industries out of wood, plastics, acryclics, ect. We offer design engineering services, product development protype services. we have a 3D printer farm. We want our communicate trust, dependability, and the value we place on client relationships.

We essentially want a credibility website. Landing page and drops downs for services we offer, capabilites, about us, contact

```html
<!DOCTYPE html>
<html lang="en">
<head>
<meta charset="utf-8">
<title>Northfield Precision – Custom Part Development</title>
<link rel="stylesheet" href="https://fonts.googleapis.com/css2?family=Oswald:wght@400;500;600&family=Nunito:wght@400;600;700&display=swap">
<style>
:root{
  --ink:#161616;
  --dark:#1c1c1c;
  --panel:#2e2e2e;
  --tile-muted:#3a3a3a;
  --light:#f1f1f1;
  --white:#ffffff;
  --line:#8a8a8a;
  --text:#333333;
  --muted:#777777;
  --steel:#5f7590;
  --spark:#e8892f;
}
*{box-sizing:border-box;margin:0;padding:0}
html,body{width:1200px;height:4283px;overflow:hidden}
body{position:relative;background:var(--light);font-family:"Nunito",sans-serif;color:var(--text)}
.abs{position:absolute}
.heading{font-family:"Oswald",sans-serif;font-weight:500;text-transform:uppercase;color:var(--ink);text-align:center;font-size:30px;letter-spacing:.2px}
.btn{position:absolute;display:flex;align-items:center;justify-content:center;font-family:"Oswald",sans-serif;font-size:14px;text-transform:uppercase;letter-spacing:.5px}
.btn-dark{background:var(--panel);color:var(--white)}
.btn-light{background:var(--white);color:var(--ink)}
.arrow-btn{position:absolute;width:40px;height:40px;background:var(--ink);display:flex;align-items:center;justify-content:center}

/* header */
.site-header{position:absolute;left:0;top:0;width:1200px;height:125px;background:var(--white)}
.brand{position:absolute;left:163px;top:44px;display:flex;align-items:center;gap:10px;font-family:"Nunito",sans-serif;font-weight:700;font-size:15px;letter-spacing:2px;color:var(--ink)}
.brand .mark{width:18px;height:18px;border:2px solid var(--ink)}
.top-contact{position:absolute;top:24px;left:597px;display:flex;gap:38px;font-size:11px;color:var(--ink);align-items:center}
.top-contact span{display:flex;align-items:center;gap:6px}
.search{position:absolute;left:905px;top:18px;width:136px;height:26px;font-size:11px;color:#aaa;display:flex;align-items:center;justify-content:space-between;padding:0 4px 0 8px}
.main-nav{position:absolute;left:411px;top:73px;display:flex;gap:27px;font-family:"Nunito",sans-serif;font-weight:700;font-size:10.5px;letter-spacing:1.6px;text-transform:uppercase;color:var(--ink)}
.quote-btn{left:881px;top:61px;width:158px;height:40px;border:2px solid var(--panel);font-family:"Nunito",sans-serif;font-weight:700;font-size:11px;letter-spacing:2px;color:var(--ink)}

/* hero */
.hero{position:absolute;left:0;top:125px;width:1200px;height:522px;background:linear-gradient(100deg,#2d3a4e 0%,#56698a 40%,#8a9bb0 62%,#6c5a4a 78%,#c77a3a 90%,#4a3a30 100%)}
.hero-title{position:absolute;left:160px;top:165px;font-family:"Oswald",sans-serif;font-weight:500;font-size:35px;line-height:45px;color:var(--white)}
.hero-sub{position:absolute;left:160px;top:260px;font-size:27px;color:var(--white)}
.hero .btn{left:161px;top:315px;width:148px;height:40px;background:var(--ink);color:var(--white);font-family:"Nunito",sans-serif;text-transform:none;font-size:13px;letter-spacing:0}

/* what we do */
.service-card{position:absolute;left:150px;top:756px;width:900px;height:324px;background:var(--white);box-shadow:0 2px 8px rgba(0,0,0,.12)}
.service{position:absolute;top:45px;width:229px}
.service .photo{height:161px;position:relative}
.service .notch{position:absolute;left:92px;bottom:0;width:0;height:0;border-left:24px solid transparent;border-right:24px solid transparent;border-bottom:26px solid var(--white)}
.service p{margin-top:24px;font-family:"Oswald",sans-serif;font-size:12.5px;line-height:22px;text-transform:uppercase;text-align:center;color:var(--ink)}

/* recent projects */
.project{position:absolute;top:1205px;width:256px;height:263px}
.project .photo{position:absolute;inset:0}
.project .caption{position:absolute;left:0;bottom:0;width:256px;height:94px;background:rgba(34,34,34,.92);clip-path:polygon(0 0,100% 0,100% 100%,0 100%)}
.project .caption p{position:absolute;left:18px;top:25px;font-family:"Oswald",sans-serif;font-size:12px;line-height:19px;color:var(--white);text-transform:uppercase}
.project .go{position:absolute;right:0;bottom:0;width:54px;height:60px;background:var(--dark);clip-path:polygon(25% 0,100% 0,100% 100%,0 100%);display:flex;align-items:center;justify-content:flex-end;padding-right:10px}

/* about */
.about-title{position:absolute;left:163px;top:1688px;font-family:"Oswald",sans-serif;font-weight:500;font-size:33px;color:var(--white)}
.about-text{position:absolute;left:163px;top:1758px;width:430px;font-size:12.5px;line-height:28.3px;color:#e6e6e6}
.stats{position:absolute;left:150px;top:2086px;width:900px;height:194px;background:var(--white);box-shadow:0 2px 8px rgba(0,0,0,.12)}
.stat{position:absolute;top:28px}
.stat .num{font-family:"Oswald",sans-serif;font-weight:500;font-size:33px;color:var(--ink);margin-top:6px;line-height:42px}
.stat .label{font-size:12.5px;color:var(--text)}

/* process */
.step{position:absolute;top:2454px;width:158px;height:158px;border-radius:50%;background:var(--white);border:1px solid #d8d8d8;display:flex;align-items:center;justify-content:center}
.step-label{position:absolute;top:2637px;width:200px;text-align:center;font-family:"Oswald",sans-serif;font-size:16px;line-height:20px;color:var(--ink);text-transform:uppercase}

/* capabilities */
.cap{position:absolute;top:2992px;width:196px;height:196px;background:var(--white);display:flex;flex-direction:column;align-items:center;padding-top:48px}
.cap span{margin-top:22px;font-family:"Oswald",sans-serif;font-weight:500;font-size:15px;color:var(--ink);text-transform:uppercase}
.cap.muted{background:var(--tile-muted)}
.cap.muted span{color:#7a7a7a}

/* contact */
.contact-card{position:absolute;left:194px;top:3515px;width:803px;height:407px;background:var(--white);overflow:hidden}
.contact-panel{position:absolute;left:0;top:0;width:352px;height:407px;background:var(--panel);clip-path:polygon(0 0,172px 0,352px 100%,0 100%)}
.contact-brand{position:absolute;left:36px;top:102px;display:flex;align-items:center;gap:8px;font-weight:700;font-size:14px;letter-spacing:2px;color:var(--white)}
.contact-brand .mark{width:16px;height:16px;border:2px solid var(--white)}
.contact-line{position:absolute;left:34px;display:flex;gap:12px;font-size:14px;line-height:18px;color:var(--white)}
.field{position:absolute;border-bottom:1px solid var(--line);font-size:10.5px;color:#999;padding-bottom:22px}
.field.active{color:var(--ink);border-bottom:2px solid var(--ink)}

/* footer */
.footer-brand{position:absolute;left:0;top:4035px;width:1200px;display:flex;justify-content:center;align-items:center;gap:12px;font-weight:700;font-size:22px;letter-spacing:4px;color:var(--white)}
.footer-brand .mark{width:24px;height:24px;border:2px solid var(--white)}
.footer-nav a{position:absolute;top:4162px;font-size:13px;color:var(--white);text-decoration:none;transform:translateX(-50%)}
.footer-rule{position:absolute;left:163px;top:4216px;width:876px;height:1px;background:#3e3e3e}
.copyright{position:absolute;left:163px;top:4243px;font-size:12px;color:#cfcfcf}
.social{position:absolute;top:4242px;width:24px;height:24px;border:1px solid #bbb}
</style>
</head>
<body>

<!-- Header -->
<header class="site-header">
  <div class="brand"><div class="mark"></div>NORTHFIELD PRECISION</div>
  <div class="top-contact">
    <span><svg width="11" height="11" viewBox="0 0 24 24" fill="none" stroke="#161616" stroke-width="2"><path d="M22 16.9v3a2 2 0 0 1-2.2 2 19.8 19.8 0 0 1-8.6-3.1 19.5 19.5 0 0 1-6-6A19.8 19.8 0 0 1 2.1 4.2 2 2 0 0 1 4.1 2h3a2 2 0 0 1 2 1.7c.1 1 .4 1.9.7 2.8a2 2 0 0 1-.5 2.1L8 9.8a16 16 0 0 0 6 6l1.3-1.3a2 2 0 0 1 2.1-.4c.9.3 1.8.6 2.8.7a2 2 0 0 1 1.7 2z"/></svg>(555) 014-2290</span>
    <span><svg width="12" height="10" viewBox="0 0 24 18" fill="none" stroke="#161616" stroke-width="2"><rect x="1" y="1" width="22" height="16"/><path d="M1 1l11 9 11-9"/></svg>info@northfieldprecision.com</span>
  </div>
  <div class="search">Search...<svg width="11" height="11" viewBox="0 0 24 24" fill="none" stroke="#161616" stroke-width="3"><circle cx="10" cy="10" r="7"/><path d="M15 15l7 7"/></svg></div>
  <nav class="main-nav"><span>Our Services ▾</span><span>Capabilites</span><span>About Us</span><span>Contact Us</span></nav>
  <div class="btn quote-btn">Request Quote</div>
</header>

<!-- Hero -->
<section class="hero" role="img" aria-label="Photo of a CNC laser cutting head throwing orange sparks over a metal sheet">
  <h1 class="hero-title">Custom Part Development<br>And Manufacturing</h1>
  <p class="hero-sub">Let's Bring Your Ideas To Life</p>
  <div class="btn">Request Quote</div>
</section>

<!-- What we do -->
<h2 class="heading abs" style="left:0;width:1150px;top:700px">What We Do</h2>
<div class="service-card">
  <div class="service" style="left:51px">
    <div class="photo" role="img" aria-label="Photo of cabinet design drawings on a desktop monitor" style="background:linear-gradient(180deg,#bfc4c9,#e8e9ea 60%,#9ea3a8)"><div class="notch"></div></div>
    <p>We offer design and assembly for<br>any cabinetry or can build cabinets<br>to specifications.</p>
  </div>
  <div class="service" style="left:335px">
    <div class="photo" role="img" aria-label="Photo of a machinist working at a milling machine" style="background:linear-gradient(160deg,#2f4a63,#5f7a91 55%,#1f2e3c)"><div class="notch"></div></div>
    <p>We also cut components for other<br>industries out of wood, plastics,<br>acrylics, etc.</p>
  </div>
  <div class="service" style="left:619px">
    <div class="photo" role="img" aria-label="Photo of a CNC router cutting a sheet on a blue work table" style="background:linear-gradient(160deg,#2a3f8a,#5a6fb8 55%,#d8dbe3)"><div class="notch"></div></div>
    <p>We offer design engineering<br>services, product development<br>protype services.</p>
  </div>
</div>

<!-- Recent projects -->
<h2 class="heading abs" style="left:0;width:1200px;top:1125px">Recent Projects</h2>
<div class="arrow-btn" style="left:121px;top:1301px"><svg width="18" height="12" viewBox="0 0 18 12" fill="none" stroke="#fff" stroke-width="1.6"><path d="M17 6H2M7 1L2 6l5 5"/></svg></div>
<div class="arrow-btn" style="left:1039px;top:1301px"><svg width="18" height="12" viewBox="0 0 18 12" fill="none" stroke="#fff" stroke-width="1.6"><path d="M1 6h15M11 1l5 5-5 5"/></svg></div>
<article class="project" style="left:196px">
  <div class="photo" role="img" aria-label="Photo of a worker grinding metal with sparks" style="background:linear-gradient(150deg,#4a4540,#a38a6c 50%,#3a3532)"></div>
  <div class="caption"><p>Lorem ipsum dolor sit amet,<br>consectetur adipiscing elit.<br>Etiam suscipit lorem.</p></div>
  <div class="go"><svg width="16" height="10" viewBox="0 0 18 12" fill="none" stroke="#fff" stroke-width="1.6"><path d="M1 6h15M11 1l5 5-5 5"/></svg></div>
</article>
<article class="project" style="left:472px">
  <div class="photo" role="img" aria-label="Photo of an operator holding a tablet beside a drilling machine" style="background:linear-gradient(150deg,#3f4a55,#9aa6b0 50%,#5a6570)"></div>
  <div class="caption"><p>Lorem ipsum dolor sit amet,<br>consectetur adipiscing elit.<br>Etiam suscipit lorem.</p></div>
  <div class="go"><svg width="16" height="10" viewBox="0 0 18 12" fill="none" stroke="#fff" stroke-width="1.6"><path d="M1 6h15M11 1l5 5-5 5"/></svg></div>
</article>
<article class="project" style="left:748px">
  <div class="photo" role="img" aria-label="Photo of a welder working beside an orange welding unit" style="background:linear-gradient(150deg,#3a3a3a,#6e6a66 50%,#c0622f 85%)"></div>
  <div class="caption"><p>Lorem ipsum dolor sit amet,<br>consectetur adipiscing elit.<br>Etiam suscipit lorem.</p></div>
  <div class="go"><svg width="16" height="10" viewBox="0 0 18 12" fill="none" stroke="#fff" stroke-width="1.6"><path d="M1 6h15M11 1l5 5-5 5"/></svg></div>
</article>
<div class="btn btn-dark" style="left:532px;top:1504px;width:136px;height:42px">View All</div>

<!-- About band -->
<svg class="abs" style="left:0;top:1557px" width="1200" height="570" viewBox="0 0 1200 570"><polygon points="0,0 600,88 1200,0 1200,570 600,462 0,570" fill="#1c1c1c"/></svg>
<h2 class="about-title">ABOUT US</h2>
<p class="about-text">Lorem ipsum dolor sit amet, consectetur adipiscing elit. Etiam suscipit lorem eget ligula tincidunt pharetra. Sed aliquam lacus et dolor tempus mollis. Etiam luctus, metus eget lobortis porttitor, arcu orci bibendum dolor, ut accumsan lacus nibh et nisi. Curabitur et pharetra orci. Sed vulputate erat risus. Sed lobortis nunc eleifend ornare ultrices. Mauris eget justo nisi. Nulla ultrices commodo orci ac vulputate. Nunc at leo quis elit tincidunt placerat. Nam lacinia rutrum varius.</p>
<div class="btn btn-light" style="left:161px;top:2011px;width:135px;height:40px">Read More</div>
<div class="abs" role="img" aria-label="Photo of a technician in a hard hat operating a CNC control panel" style="left:643px;top:1687px;width:356px;height:369px;background:linear-gradient(110deg,#6a6f78,#c9ccd2 35%,#2b3a5c 65%,#d9dbe0)"></div>

<div class="stats">
  <div class="stat" style="left:46px">
    <svg width="44" height="40" viewBox="0 0 44 40" fill="none" stroke="#161616" stroke-width="2"><rect x="2" y="10" width="40" height="28" rx="2"/><path d="M15 10V4h14v6M2 21h40M19 18h6v6h-6z"/></svg>
    <div class="num">20+</div><div class="label">Years of Experience</div>
  </div>
  <div class="stat" style="left:261px">
    <svg width="44" height="40" viewBox="0 0 44 40" fill="none" stroke="#161616" stroke-width="2"><path d="M8 2v38M8 4h26v18H8M8 9h26M8 14h26M8 19h12"/><rect x="4" y="36" width="10" height="3"/></svg>
    <div class="num">100%</div><div class="label">Made in America</div>
  </div>
  <div class="stat" style="left:475px">
    <svg width="44" height="40" viewBox="0 0 44 40" fill="none" stroke="#161616" stroke-width="2"><circle cx="22" cy="20" r="18"/><path d="M10 10c5 3 6 8 2 12s2 9 6 12M28 4c-3 5 2 8 6 9s3 8-1 12"/></svg>
    <div class="num">GLOBAL</div><div class="label">Servicimg  the Globe</div>
  </div>
  <div class="stat" style="left:689px">
    <svg width="44" height="40" viewBox="0 0 44 40" fill="none" stroke="#161616" stroke-width="2"><circle cx="22" cy="14" r="11"/><circle cx="22" cy="14" r="6"/><path d="M15 23l-4 15 6-3 3 5M29 23l4 15-6-3-3 5"/></svg>
    <div style="margin-top:8px;width:66px;height:28px;background:#161616"></div>
    <div class="label" style="margin-top:10px">Industry Standatrds Met</div>
  </div>
</div>

<!-- Process -->
<h2 class="heading abs" style="left:0;width:1200px;top:2372px">Our Process</h2>
<div class="step" style="left:200px"><svg width="70" height="70" viewBox="0 0 70 70" fill="none" stroke="#161616" stroke-width="2.4"><path d="M14 30a21 21 0 0 1 42 0M10 30h50v6H10zM30 10v12M40 10v12M18 36c2 14 10 22 17 22s15-8 17-22"/><path d="M10 44l-4 4 5 5M60 44l4 4-5 5"/></svg></div>
<div class="step" style="left:415px"><svg width="70" height="70" viewBox="0 0 70 70" fill="none" stroke="#161616" stroke-width="2.4"><path d="M35 8l26 13-26 13L9 21zM9 31l26 13 26-13M9 41l26 13 26-13"/></svg></div>
<div class="step" style="left:627px"><svg width="70" height="70" viewBox="0 0 70 70" fill="none" stroke="#161616" stroke-width="2.4"><path d="M10 10h50M22 10v10h26V10M30 20v8h10v-8M35 28v10M8 54h54v6H8zM35 42v6M24 48h22"/></svg></div>
<div class="step" style="left:840px"><svg width="70" height="70" viewBox="0 0 70 70" fill="none" stroke="#161616" stroke-width="2.4"><path d="M18 20h28v28H18M46 28h10l8 10v10H46zM6 28h10M10 36h8M4 44h10"/><circle cx="26" cy="50" r="4"/><circle cx="54" cy="50" r="4"/></svg></div>
<svg class="abs" style="left:366px;top:2524px" width="40" height="18" viewBox="0 0 40 18" fill="#999"><path d="M2 2l8 7-8 7h4l8-7-8-7zM14 2l8 7-8 7h4l8-7-8-7zM26 2l8 7-8 7h4l8-7-8-7z"/></svg>
<svg class="abs" style="left:579px;top:2524px" width="40" height="18" viewBox="0 0 40 18" fill="#999"><path d="M2 2l8 7-8 7h4l8-7-8-7zM14 2l8 7-8 7h4l8-7-8-7zM26 2l8 7-8 7h4l8-7-8-7z"/></svg>
<svg class="abs" style="left:792px;top:2524px" width="40" height="18" viewBox="0 0 40 18" fill="#999"><path d="M2 2l8 7-8 7h4l8-7-8-7zM14 2l8 7-8 7h4l8-7-8-7zM26 2l8 7-8 7h4l8-7-8-7z"/></svg>
<div class="step-label" style="left:179px">Application<br>Engineering</div>
<div class="step-label" style="left:394px">Material<br>Selection</div>
<div class="step-label" style="left:606px">Part<br>Fabrication</div>
<div class="step-label" style="left:819px">Delivery</div>
<div class="btn btn-dark" style="left:532px;top:2706px;width:136px;height:42px">Get Started</div>

<!-- Capabilities band -->
<svg class="abs" style="left:0;top:2767px" width="1200" height="643" viewBox="0 0 1200 643"><polygon points="0,0 600,67 1200,0 1200,540 600,643 0,540" fill="#1c1c1c"/></svg>
<h2 class="heading abs" style="left:0;width:1200px;top:2925px;color:#fff;font-size:33px">Our Capabilites</h2>
<div class="cap muted" style="left:0"><svg width="56" height="60" viewBox="0 0 56 60" fill="none" stroke="#7a7a7a" stroke-width="2.4"><path d="M8 6h40v8H8zM20 14v10h16V14M24 24v22l4 10 4-10V24"/></svg><span>Reaming</span></div>
<div class="cap" style="left:201px"><svg width="56" height="60" viewBox="0 0 56 60" fill="none" stroke="#161616" stroke-width="2.4"><path d="M6 4h44M16 4v12h24V4M22 16v10h12V16M28 26v12M4 48h48v6H4zM18 42h20"/></svg><span>Parting/Cutting</span></div>
<div class="cap" style="left:402px"><svg width="56" height="60" viewBox="0 0 56 60" fill="none" stroke="#161616" stroke-width="2.4"><circle cx="28" cy="32" r="14"/><circle cx="28" cy="32" r="4"/><path d="M10 10l16 18M6 50h44v6H6z"/></svg><span>Facing</span></div>
<div class="cap" style="left:603px"><svg width="56" height="60" viewBox="0 0 56 60" fill="none" stroke="#161616" stroke-width="2.4"><path d="M24 4h6v26h-6zM20 30h14v8H20zM6 42h44v8H6zM10 50v6M46 50v6M38 36h10v6"/></svg><span>Turning</span></div>
<div class="cap" style="left:804px"><svg width="56" height="60" viewBox="0 0 56 60" fill="none" stroke="#161616" stroke-width="2.4"><path d="M10 56h36v-8H10zM18 48V34l12-12 10 6M30 22l6-14 8 4-4 12"/><circle cx="30" cy="22" r="4"/><circle cx="18" cy="34" r="4"/></svg><span>Boring</span></div>
<div class="cap muted" style="left:1005px"><svg width="56" height="60" viewBox="0 0 56 60" fill="none" stroke="#7a7a7a" stroke-width="2.4"><path d="M20 4h16v10H20zM28 14v18M6 30h44v22H6zM6 41h44M17 30v22M39 30v22"/></svg><span>Drilling</span></div>
<div class="arrow-btn" style="left:154px;top:3070px"><svg width="18" height="12" viewBox="0 0 18 12" fill="none" stroke="#fff" stroke-width="1.6"><path d="M17 6H2M7 1L2 6l5 5"/></svg></div>
<div class="arrow-btn" style="left:1006px;top:3070px"><svg width="18" height="12" viewBox="0 0 18 12" fill="none" stroke="#fff" stroke-width="1.6"><path d="M1 6h15M11 1l5 5-5 5"/></svg></div>
<div class="btn btn-light" style="left:532px;top:3228px;width:136px;height:41px">Contact Us</div>

<!-- Footer band -->
<div class="abs" style="left:0;top:3798px;width:1200px;height:485px;background:var(--dark)"></div>

<!-- Contact -->
<h2 class="heading abs" style="left:0;width:1200px;top:3465px">Contact Us</h2>
<div class="contact-card">
  <div class="contact-panel"></div>
  <div class="contact-brand"><div class="mark"></div>NORTHFIELD</div>
  <div class="contact-line" style="top:190px"><svg width="14" height="14" viewBox="0 0 24 24" fill="#fff"><path d="M22 16.9v3a2 2 0 0 1-2.2 2A19.8 19.8 0 0 1 2.1 4.2 2 2 0 0 1 4.1 2h3a2 2 0 0 1 2 1.7l.7 2.8-1.8 3.3a16 16 0 0 0 6 6l3.3-1.8 2.8.7a2 2 0 0 1 1.9 2.2z"/></svg>(555) 014-2290</div>
  <div class="contact-line" style="top:232px"><svg width="14" height="12" viewBox="0 0 24 18" fill="#fff"><path d="M0 0h24v18H0z"/><path d="M1 1l11 9 11-9" stroke="#2e2e2e" stroke-width="2" fill="none"/></svg>info@northfieldprecision.com</div>
  <div class="contact-line" style="top:276px"><svg width="14" height="18" viewBox="0 0 14 18" fill="#fff"><path d="M7 0a7 7 0 0 0-7 7c0 5 7 11 7 11s7-6 7-11a7 7 0 0 0-7-7zm0 10a3 3 0 1 1 0-6 3 3 0 0 1 0 6z"/></svg><span>123, Building Name, Street<br>City, State XY 123456</span></div>
  <div class="contact-line" style="top:345px;font-size:13px;text-decoration:underline;left:36px">VIEW DIRECTIONS</div>
  <div class="field active" style="left:320px;top:72px;width:215px">First Name*</div>
  <div class="field" style="left:558px;top:72px;width:215px">Last Name*</div>
  <div class="field" style="left:320px;top:148px;width:215px">Phone Number*</div>
  <div class="field" style="left:558px;top:148px;width:215px">Postal Code*</div>
  <div class="field" style="left:320px;top:225px;width:453px">Message*</div>
  <div class="btn btn-dark" style="left:655px;top:294px;width:100px;height:38px;background:var(--ink)">Submit</div>
</div>

<!-- Footer -->
<div class="footer-brand"><div class="mark"></div>NORTHFIELD PRECISION</div>
<nav class="footer-nav">
  <a href="#" style="left:261px">Home</a>
  <a href="#" style="left:415px">About Us</a>
  <a href="#" style="left:575px">Services</a>
  <a href="#" style="left:743px">Capabilities</a>
  <a href="#" style="left:921px">Contact Us</a>
</nav>
<div class="footer-rule"></div>
<p class="copyright">© 2023 Northfield Precision. All Rights Reserved.</p>
<div class="social" style="left:899px"></div>
<div class="social" style="left:937px"></div>
<div class="social" style="left:975px"></div>
<div class="social" style="left:1013px"></div>

</body>
</html>
```